Software Company Banner Ad

We need a banner ad in two sizes. 728x90 and 300x250.
They should have strong similarity to the following ads:
http://www.quellara.com/search/results?brand[0]=zorvik&ad=4812096
http://www.quellara.com/search/results?brand[0]=tralvenco&ad=4826173
Idea will be very similar. We want the same grey color, white text, and a realistic owl that blinks. The owl should have dramatic, bright, yellow eyes. The text will animate "from the top" as in the example. Though the logo animation will be different, all text and non-logo animation should match the animation in the example advertisements. The text will rotate between the following four sentences and images.
Looking for a provider of procurement cloud apps?
[Images - attached below]
The experts really liked our PLW booth.
Get great results with every procurement. [Learn more]
There are three vector files attached below. Feel free to change the colors as necessary to match the color scheme of the ad. We need one 2013 and one 2014 award in the ad.
The awards could appear simultaneously, could swap with each other or could appear in succession. Animation is acceptable.
There is an additional vector file with the company logo. The company logo should go where the Zorvik logo is in horizontal ad. The company logo should go where the Tralvenco logo is in the block ad. The example ad has two logos. We will only need one logo on our ads. The logo should be changed to the color of the text used for the ad (white).
The owls eyes should slowly blink two times (as in the example).
The owl eyes should immediately grab someone's attention and all colors should compliment these eyes.
The [Learn more] button should have animation. The button should match the color of the owl's eyes. There should be a line/gleam/glare of light that travels across the button. The button should be embossed with the subtle animation occurring each time it appears.
Ads should be done with flash. We will need the source files and the names of any fonts used at the end of the project.
Thank you and please do not hesitate to contact with any questions.
Updates
Project Deadline Extended
Reason: We have contacted several photographers to see if the alternative owl images are available on pixHarb, Framelodgery or similar. The duration extension is to accommodate this.
Target Market(s)
Target customers are procurement department employees of large companies.
Industry/Entity Type
It Company

```html
<!DOCTYPE html>
<html lang="en">
<head>
<meta charset="utf-8">
<title>Velqor Procurement Banner</title>
<link href="https://fonts.googleapis.com/css2?family=Open+Sans:wght@400;600;700&display=swap" rel="stylesheet">
<style>
  :root {
    --panel-grey: #5b5b5b;
    --panel-grey-dark: #4e4e4e;
    --text-white: #ffffff;
    --badge-white: #f4f4f4;
    --badge-red: #d8261c;
    --badge-gold: #e7a21a;
    --button-top: #fbb03b;
    --button-bottom: #e2761a;
    --button-edge: #b85d10;
    --photo-black: #070605;
    --photo-dark: #1a140e;
    --photo-feather: #4a3a2a;
    --photo-tan: #7a634a;
    --photo-light: #a48a6c;
    --photo-amber: #c9701a;
  }
  html, body {
    margin: 0;
    padding: 0;
    overflow: hidden;
    background: #ffffff;
  }
  .banner {
    position: relative;
    width: 1200px;
    height: 148px;
    overflow: hidden;
    font-family: "Open Sans", Arial, sans-serif;
    background: var(--panel-grey);
  }
  .message-panel {
    position: absolute;
    left: 0;
    top: 0;
    width: 636px;
    height: 148px;
    background: linear-gradient(180deg, var(--panel-grey) 0%, var(--panel-grey-dark) 100%);
  }
  .brand-name {
    position: absolute;
    left: 13px;
    top: 14px;
    margin: 0;
    color: var(--text-white);
    font-weight: 700;
    font-size: 21px;
    letter-spacing: 1px;
    line-height: 1;
  }
  .headline {
    position: absolute;
    left: 30px;
    top: 53px;
    width: 440px;
    margin: 0;
    color: var(--text-white);
    font-weight: 400;
    font-size: 29px;
    line-height: 37px;
    text-align: center;
  }
  .award {
    position: absolute;
    top: 26px;
    width: 60px;
    height: 56px;
  }
  .award-2013 { left: 487px; }
  .award-2014 { left: 566px; }
  .learn-more {
    position: absolute;
    left: 495px;
    top: 91px;
    width: 116px;
    height: 33px;
    border: 1px solid var(--button-edge);
    border-radius: 4px;
    background: linear-gradient(180deg, var(--button-top) 0%, var(--button-bottom) 100%);
    box-shadow: inset 0 1px 0 rgba(255,255,255,0.45), 0 1px 2px rgba(0,0,0,0.35);
    color: var(--text-white);
    font-family: "Open Sans", Arial, sans-serif;
    font-weight: 600;
    font-size: 17px;
    line-height: 31px;
    text-align: center;
    text-decoration: none;
    text-shadow: 0 1px 1px rgba(0,0,0,0.3);
  }
  .owl-photo {
    position: absolute;
    left: 636px;
    top: 0;
    width: 564px;
    height: 148px;
    background:
      radial-gradient(ellipse 30% 60% at 58% 45%, rgba(201,112,26,0.45) 0%, transparent 70%),
      radial-gradient(ellipse 30% 60% at 85% 45%, rgba(201,112,26,0.45) 0%, transparent 70%),
      radial-gradient(ellipse 22% 55% at 72% 20%, var(--photo-light) 0%, transparent 80%),
      radial-gradient(ellipse 55% 110% at 72% 55%, var(--photo-tan) 0%, var(--photo-feather) 45%, var(--photo-dark) 75%, transparent 95%),
      linear-gradient(90deg, var(--photo-black) 0%, var(--photo-black) 18%, var(--photo-dark) 40%, var(--photo-feather) 100%);
  }
</style>
</head>
<body>
  <div class="banner">
    <div class="message-panel">
      <p class="brand-name">VELQOR</p>
      <h1 class="headline">Get great results with every procurement!</h1>

      <svg class="award award-2013" viewBox="0 0 60 56" aria-hidden="true">
        <rect x="1" y="1" width="58" height="54" rx="3" fill="var(--badge-white)"/>
        <rect x="9" y="14" width="42" height="22" fill="var(--badge-red)"/>
        <rect x="15" y="42" width="30" height="9" fill="var(--badge-gold)"/>
      </svg>
      <svg class="award award-2014" viewBox="0 0 60 56" aria-hidden="true">
        <rect x="1" y="1" width="58" height="54" rx="3" fill="var(--badge-white)"/>
        <rect x="9" y="14" width="42" height="22" fill="var(--badge-red)"/>
        <rect x="15" y="42" width="30" height="9" fill="var(--badge-gold)"/>
      </svg>

      <a class="learn-more" href="#">learn more&gt;</a>
    </div>

    <div class="owl-photo" role="img" aria-label="Close-up photograph of a brown-feathered owl with bright orange eyes against a black background"></div>
  </div>
</body>
</html>
```